Thornbury Spa

We are a large Miami Beach spa and salon. I am still building our website but you can use it as a resource to gain a better understanding of who we are ....www.velloraspa-studio.com.

We offer a comprehensive list of services in hair, nails, massage, skin care, tanning, spray tanning and waxing and we offer high quality products for skin care, tanning and hair. We are open 7 days.

We would like to see a clean and simple menu that looks a lot like the one from "The Spa at Larkwood." In particular, we have a copy of a menu from their West Hollywood, CA location that is just beautiful. In the uploaded content you will see a sampling of that menu. We would like to see greys, blacks, silvers, whites and warm colors like reds and oranges. We specifically attempt to remain gender neutral so that we don't attract only girls (with pink colors and flowers etc). The final design should convey a simple, clean, friendly environment and the final product should be sized such that it is 1.) portable and 2.) inexpensive to print. We will be running thousands of these at a time so cost of printing is a consideration.

The booklet consists of two parts: one part is the standard menu with descriptions of services and products and photos etc (think of this as the sales piece that convinces a potential customer to visit) and will be stapled together like you would expect a small menu to be and should resemble the Larkwood menu. The prices should not be included in this part of the booklet that will be printed and stapled. The other part is a single insert and is removable and replaceable. I want this removable insert placed in the last page of the book in a folder pocket or something else that you can think of so that when it's time to change prices here that I am not throwing away all of the booklets....I am only replacing the inserts at the end of the menu booklet. Please design this single page insert so that should a customer remove it from the booklet and keep it, that it stands alone with our name, logo, website and phone number. This page can and probably will have to be 2 sided.

At the back of the booklet, I also want the polices to be printed in one page (think fine print in any sort of business dealing.)

With regard to the look and feel slider of economical v upmarket...we definitely want to convey we deliver upmarket services at reasonable prices. Think, world class services and products at reasonable, everyday prices.

With regard to the uploaded files:
I uploaded both EPS and TIF formats. The colors in those files are not the palette we want at all. The colors we want use for the circular logo must match the standard colors as depicted in the uploaded file "Thornburytanrooms"

Target Market(s)

The target market is the average 20-35 year old in Miami Beach that cares about their appearance. The range of clientele is quite diverse.

Industry/Entity Type

Environment

Requirements
Must have
• It must have elegant and simple photographs that relate to the services being offered. We are selling a service set and an environment...so this menu should be reflect that goal. The logo should be repeated often throughout the book but in subtle ways.

Stock photos are fine as long as they don't seem obviously stock.

Should not have
• Nothing buddha like. Nothing themed. It should be all inclusive and not seek to identify with any particular group or gender.

Nothing that fits the stereotype of "Miami Beach." We want to represent ourselves in the same category as the best spas in the world because we moving everything we do in that direction. Think class!

```html
<!DOCTYPE html>
<html lang="en">
<head>
<meta charset="utf-8">
<title>Thornbury Spa – Nails Menu</title>
<link rel="stylesheet" href="https://fonts.googleapis.com/css2?family=Questrial&family=Noto+Sans:wght@400&display=swap">
<style>
  :root{
    --charcoal:#2a2a2b;
    --charcoal-light:#3d3d3f;
    --band-light:#8d8d8f;
    --band-dark:#4a4a4c;
    --bar:#b9b9bb;
    --bar-text:#3a3a3c;
    --body-text:#e6e6e6;
    --white:#ffffff;
    --mauve-light:#d3b6d3;
    --mauve-dark:#8c6a8c;
  }
  *{margin:0;padding:0;box-sizing:border-box}
  html,body{width:1200px;height:423px;overflow:hidden;background:var(--charcoal)}
  .spread{
    position:relative;width:1200px;height:423px;overflow:hidden;
    background:radial-gradient(ellipse 70% 80% at 62% 55%, var(--charcoal-light) 0%, var(--charcoal) 70%);
    font-family:'Noto Sans',sans-serif;
  }
  .accent-band{
    position:absolute;inset:0;
    clip-path:polygon(0 0,400px 0,488px 423px,0 423px);
    background:linear-gradient(180deg,var(--mauve-light),var(--mauve-dark));
  }
  .salon-photo{
    position:absolute;inset:0;
    clip-path:polygon(0 0,376px 0,460px 423px,0 423px);
    background:
      radial-gradient(ellipse 40% 35% at 55% 25%, #f3dcf0 0%, rgba(243,220,240,0) 70%),
      linear-gradient(180deg,#6b5a52 0%,#c9b8b0 30%,#e8e2da 55%,#cfc4b6 80%,#a89482 100%);
  }
  .ghost-title{
    position:absolute;left:20px;top:-6px;
    font-family:'Questrial',sans-serif;font-size:148px;letter-spacing:2px;
    color:rgba(255,255,255,.55);line-height:1;
  }
  .brand{
    position:absolute;left:468px;top:122px;width:80px;text-align:center;
    font-family:'Questrial',sans-serif;color:#cfcfcf;
  }
  .brand-mark{width:20px;height:20px;border-radius:50%;border:1.5px solid #cfcfcf;margin:0 auto 6px}
  .brand-name{font-size:11px;letter-spacing:1px;line-height:1.2}
  .title-band{
    position:absolute;left:416px;top:22px;width:784px;height:58px;
    background:linear-gradient(90deg,rgba(74,74,76,0) 0%,var(--band-dark) 25%,var(--band-light) 100%);
  }
  .menu-title{
    position:absolute;right:40px;top:14px;
    font-family:'Questrial',sans-serif;font-size:60px;letter-spacing:1px;color:var(--white);line-height:1;
  }
  .service{position:absolute;width:258px}
  .service h2{
    width:158px;height:11px;background:var(--bar);
    font-family:'Questrial',sans-serif;font-weight:400;font-size:10px;letter-spacing:1.2px;
    color:var(--bar-text);text-align:center;line-height:11px;margin-bottom:9px;
  }
  .service p{font-size:7.4px;line-height:1.42;color:var(--body-text);text-align:justify}
  .col-a{left:636px}
  .col-b{left:906px;width:262px}
  .row-1{top:98px}
  .row-2{top:200px}
  .row-3{top:323px}
  .row-3 h2{margin-bottom:13px}
</style>
</head>
<body>
<main class="spread">
  <div class="accent-band"></div>
  <div class="salon-photo" role="img" aria-label="Photo of the nail salon with cream pedicure chairs, floor lamps and warm lighting"></div>
  <div class="ghost-title">NAILS</div>

  <div class="brand">
    <div class="brand-mark"></div>
    <div class="brand-name">THORNBURY SPA</div>
  </div>

  <div class="title-band"><h1 class="menu-title">NAILS MENU</h1></div>

  <section class="service col-a row-1">
    <h2>THE CLASSIC</h2>
    <p>Our Classic option is just what your nails need on a regular basis. We start with a purifying and thorough soak to soften your nails and cuticles. We then follow with an aromatic, exfoliating massage of the hands and the feet, designed to smooth and soften your hands and feet. We remove your existing laquer, groom and oil your cuticles, shape and buff your nails and finish with the application of your favorite nail lacquer.</p>
  </section>

  <section class="service col-b row-1">
    <h2>THE EXPRESS</h2>
    <p>If you are in a mad rush but absolutely need to pay a few minutes' attention to your hands and feet, we have the perfect option. We include just the essentials- removal of existing nail lacquer, a quick soak, cuticle grooming, nail shaping and the application of your favorite lacquer. This option will get you in and out in no time!</p>
  </section>

  <section class="service col-a row-2">
    <h2>GELVARA</h2>
    <p>For those who get caught up and go too long between visits, we definitely suggest Gelvara. This unique polish is resistant to chipping, maintains an incredible shine and can last up to 21 days. We begin this option with a purifying and thorough soak to soften your nails and cuticles. We follow with an aromatic, exfoliating massage of the hands and the feet, designed to smooth and soften your hands or feet. We remove your existing laquer, groom and oil your cuticles, shape your nails and finish with your chosen Gelvara colors.</p>
  </section>

  <section class="service col-b row-2">
    <h2>THE ULTIMATE</h2>
    <p>If you want to give your hands and feet a little extra attention, you have to experience our spa treatment. Like our Classic treatment, we remove your existing polish, groom and oil your cuticles, shape and buff your nails and finish with the application of your favorite nail lacquer. From there, we massage your forearms and hands, calves and feet, incorporating warm towels and hot stones. We finish with a paraffin hand treatment, intended to leave your hands silky smooth, and we include chemical callus removal.</p>
  </section>

  <section class="service col-a row-3">
    <h2>NATURAL NAIL OVERLAYS</h2>
    <p>Use of natural nail overlays allows your nails to grow, prevent damage and maintain a beautiful look. Let our experienced and trained nail technicians recommend the overlay that fits your lifestyle, occupation and desired look.</p>
  </section>

  <section class="service col-b row-3">
    <h2>NAIL BAR POLISHING</h2>
    <p>Especially designed for those in a rush! We'll remove existing lacquer, apply a fresh coat of your favorite lacquer and you'll finish with a quick dry to get you on your way.</p>
  </section>
</main>
</body>
</html>
```